The Lantern Guild Pitchdeck Template

The Lantern Guild would like a branded pitch deck template design for members to use when presenting their projects and proposals. The deck should include 10-15 different slide designs, each with the same branded theme, but with a variety of icon graphics and other design features that will empower members to easily create a beautiful pitch deck just by adding written content.

Please visit lanternguildhq.org to get a sense for our branding - purple, space, galaxy, white font and the planetary logo are some commonalities.

Here are 2 google drive links with some additional designs

https://files.boxmeadow.net/share/f/8QzrTa2Lk5VbNw7cHyP0dJe3sUmXg4RiF

https://files.boxmeadow.net/share/f/3Kd9-Rm6Tq2-yLvBn051fopwxhcT_zj7

```html
<!DOCTYPE html>
<html lang="en">
<head>
<meta charset="utf-8">
<title>The Lantern Guild — Pitch Deck Template</title>
<link rel="stylesheet" href="https://fonts.googleapis.com/css2?family=Montserrat:wght@600;700&family=Open+Sans:wght@400;600&family=Roboto+Slab:wght@300;400;700&display=swap">
<style>
  :root{
    --page:#ffffff;
    --space-deep:#07071a;
    --space-mid:#171438;
    --nebula:#3a1d5e;
    --purple:#7b2fc9;
    --violet:#a56be6;
    --panel-dark:#1a0f2b;
    --text-light:#ffffff;
    --text-soft:#d9d3e6;
    --ink:#26232e;
    --ink-soft:#55515e;
  }
  *{box-sizing:border-box;margin:0;padding:0}
  html,body{width:1200px;height:4056px;overflow:hidden;background:var(--page)}
  body{position:relative;font-family:"Open Sans",Arial,sans-serif;color:var(--text-light)}
  .slide{position:absolute;left:48px;width:1104px;height:621px;overflow:hidden;background:var(--space-deep)}
  .abs{position:absolute}
  .brand{position:absolute;left:48px;top:32px;z-index:3;font-family:"Montserrat",Arial,sans-serif;color:var(--text-light)}
  .brand-name{font-size:38px;font-weight:700;letter-spacing:10px;line-height:1}
  .brand-sub{font-size:11px;font-weight:600;letter-spacing:3.2px;margin-top:6px;text-transform:uppercase}
  .slide-title{font-family:"Roboto Slab",Georgia,serif;font-weight:700;text-transform:uppercase;letter-spacing:1px}
  .bg-space{position:absolute;inset:0}
  /* slide 1 */
  .s-welcome .bg-space{background:radial-gradient(ellipse at 50% 85%,#3d2a5f 0%,rgba(40,25,70,.5) 30%,transparent 60%),radial-gradient(ellipse at 20% 30%,#1d1a44 0%,transparent 55%),linear-gradient(180deg,#0a0a22 0%,#15112e 60%,#241634 100%)}
  .welcome-block{position:absolute;left:0;right:0;top:190px;text-align:center;font-family:"Roboto Slab",Georgia,serif}
  .welcome-kicker{font-size:38px;font-weight:300;letter-spacing:1px}
  .welcome-name{font-size:58px;font-weight:700;letter-spacing:2px;margin-top:6px}
  .welcome-sub{font-size:34px;font-weight:300;margin-top:4px;text-transform:uppercase}
  .accent-rule{width:84px;height:3px;background:var(--purple);margin:22px auto 0}
  .year{position:absolute;right:48px;top:522px;font-family:"Montserrat",Arial,sans-serif;font-weight:700;font-size:16px;color:var(--violet)}
  .social{position:absolute;right:48px;top:552px;display:flex;gap:10px}
  .social span{width:30px;height:30px;border:1.5px solid var(--text-light);border-radius:50%;display:flex;align-items:center;justify-content:center;font-size:8px;font-weight:600}
  /* slide 2 */
  .s-about .bg-space{background:radial-gradient(ellipse at 70% 45%,#5b3d8f 0%,#2c2060 30%,transparent 65%),radial-gradient(ellipse at 95% 90%,#3f2a6a 0%,transparent 45%),linear-gradient(120deg,#060618 0%,#100f2c 45%,#1c1640 100%)}
  .about-title{left:32px;top:164px;font-size:42px}
  .about-copy{left:32px;top:222px;width:352px;font-size:11.5px;line-height:1.55;color:var(--text-soft)}
  .about-copy p{margin-bottom:10px}
  .channels{left:32px;top:524px;display:flex;gap:14px}
  .channels span{display:flex;align-items:center;gap:6px;font-size:11px;font-weight:600;color:#7fb0ff}
  .channels i{width:14px;height:14px;border-radius:50%;background:#5a7df0;display:block}
  .emblem{left:520px;top:90px;width:480px;height:400px;display:flex;align-items:center;justify-content:center;gap:24px}
  .emblem i{width:120px;height:120px;border-radius:50%;background:var(--text-light);display:block}
  .emblem span{font-family:"Montserrat",Arial,sans-serif;font-weight:700;font-size:96px;letter-spacing:8px}
  /* slide 3 */
  .s-intent{background:var(--page)}
  .intent-visual{left:0;top:0;width:592px;height:621px;background:radial-gradient(circle at 50% 48%,#f4a95a 0%,#c2477a 18%,#3b6fd1 32%,#1a1440 55%),linear-gradient(180deg,#0d0b26,#2a1535)}
  .intent-title{left:632px;top:58px;font-size:44px;color:var(--ink);font-weight:400}
  .intent-copy{left:632px;top:124px;width:436px;font-size:12.2px;line-height:1.72;color:var(--ink-soft);text-align:justify}
  /* slide 4 */
  .s-vision .bg-space{background:radial-gradient(ellipse at 50% 100%,#2a1c44 0%,transparent 60%),linear-gradient(180deg,#0b0a1f,#120f28)}
  .vision-title{left:0;right:0;top:60px;text-align:center;font-size:40px}
  .vision-card{position:absolute;width:290px;text-align:center}
  .vision-card .photo{width:290px;height:248px}
  .vision-card h3{font-family:"Roboto Slab",Georgia,serif;font-weight:700;font-size:24px;margin-top:40px;letter-spacing:1px}
  .vision-card p{font-size:11.5px;line-height:1.5;color:var(--text-soft);margin:8px 18px 0}
  .card-people{left:84px;top:164px}
  .card-planet{left:408px;top:128px}
  .card-planet h3{margin-top:36px}
  .card-peace{left:730px;top:164px}
  .photo-people{background:linear-gradient(180deg,#5e4aa6 0%,#7b5cc0 45%,#4a2f7a 100%)}
  .photo-planet{background:radial-gradient(circle at 50% 55%,#4f8fd6 0%,#2b5aa0 28%,#3a2a78 45%,#7a4fb8 70%,#1d1446 100%)}
  .photo-peace{background:linear-gradient(180deg,#f2b35a 0%,#e56a3c 45%,#6b2a3e 100%)}
  /* slide 5 */
  .s-partners .bg-space{background:radial-gradient(ellipse at 50% 110%,#a97fb8 0%,#5a3a7a 25%,transparent 55%),linear-gradient(180deg,#0b0a1f 0%,#140f2c 70%,#24183a 100%)}
  .partners-title{left:0;right:0;top:68px;text-align:center;font-size:40px}
  .partner{position:absolute;width:150px;text-align:center}
  .hex{width:112px;height:124px;margin:0 auto;clip-path:polygon(50% 0,100% 25%,100% 75%,50% 100%,0 75%,0 25%)}
  .partner span{display:block;margin-top:10px;font-family:"Montserrat",Arial,sans-serif;font-weight:700;font-size:10px;letter-spacing:1px}
  .hex-violet{background:radial-gradient(circle,#6a4cc6,#1d1646)}
  .hex-green{background:#1b1430;box-shadow:inset 0 0 0 6px #2fd06b}
  .hex-gold{background:#111}
  .hex-blue{background:#1e3a78}
  .hex-white{background:#f3f3f3}
  .hex-night{background:#181a2c}
  /* slide 6 */
  .s-laws{background:var(--panel-dark)}
  .laws-visual{left:0;top:0;width:544px;height:621px;background:radial-gradient(circle at 55% 55%,#b0a2c8 0%,#6f5a9a 20%,transparent 45%),linear-gradient(180deg,#2a1d4a 0%,#7a3f6a 55%,#d7745a 80%,#2a1630 100%)}
  .laws-title{left:588px;top:56px;font-size:40px}
  .laws-copy{left:588px;top:114px;width:470px;font-size:12px;line-height:1.6;color:var(--text-soft)}
  .thanks-title{left:588px;top:290px;font-size:40px}
  .contact{position:absolute;left:588px;display:flex;align-items:center;gap:16px;font-size:12px;color:var(--text-soft)}
  .contact .ico{width:36px;height:36px;border-radius:50%;background:var(--text-light);display:flex;align-items:center;justify-content:center;flex:none}
  .contact-addr{top:372px;width:440px}
  .contact-phone{top:436px}
  .contact-mail{top:500px}
</style>
</head>
<body>

<!-- Slide 1: Welcome -->
<section class="slide s-welcome" style="top:32px">
  <div class="bg-space" role="img" aria-label="Deep space starfield with faint purple nebula glow"></div>
  <div class="brand"><div class="brand-name">LUMEN</div><div class="brand-sub">Lantern Circle</div></div>
  <div class="welcome-block">
    <div class="welcome-kicker">WELCOME TO</div>
    <div class="welcome-name">LUMEN</div>
    <div class="welcome-sub">Lantern Circle</div>
    <div class="accent-rule"></div>
  </div>
  <div class="year">2022</div>
  <div class="social"><span>Orbit</span><span>Pulse</span><span>Glow</span></div>
</section>

<!-- Slide 2: Who are we -->
<section class="slide s-about" style="top:688px">
  <div class="bg-space" role="img" aria-label="Purple galaxy nebula with a lone figure standing on a rocky horizon"></div>
  <div class="brand"><div class="brand-name">LUMEN</div><div class="brand-sub">Lantern Circle</div></div>
  <h2 class="abs slide-title about-title">Who are we</h2>
  <div class="abs about-copy">
    <p>The Lantern Guild is a spiritual, conscious and regenerative non-profit organization established for furthering the spiritualism, enlightenment, spiritual realization, and general welfare of people throughout the world, the betterment of life on planet Earth, and other spiritual, environmental, humanitarian, and charitable purposes.</p>
    <p>Buddhism, Christianity, Hinduism, Islam, Judaism and other religions are belief systems. The Universe exists whether you believe in it or not.</p>
    <p>We are the Universe, and so are you.</p>
  </div>
  <div class="abs channels"><span><i></i>Hearth</span><span><i></i>Relay</span></div>
  <div class="abs emblem"><i></i><span>LUMEN</span></div>
</section>

<!-- Slide 3: Intentions -->
<section class="slide s-intent" style="top:1352px">
  <div class="abs intent-visual" role="img" aria-label="Glowing neon peace symbol against a dusk sky over a treeline"></div>
  <div class="brand"><div class="brand-name">LUMEN</div><div class="brand-sub">Lantern Circle</div></div>
  <h2 class="abs slide-title intent-title">Intentions</h2>
  <p class="abs intent-copy">The Lantern Guild, members, missionaries, stewards, sponsors, partners, and donors are working on various initiatives to fulfill our intentions. As a collective we are focusing on every area; from education, healthcare, economics, finance, governance &amp; technology, to space travel, art, music, and transformational experiences. Our mission is to protect the earth &amp; the future, land and food, to create a system that supports the people and the planet, to redistribute wealth, protect human rights, serve, create and implement the conscious economy. We are focused on building a global community, transforming local environments, integration with indigenous tribes and the celebration of society. We are interested in new paradigm schools and universities, incubators for regenerative technology, natural medicine, empowering micro-industries, entrepreneurs, investors, inventors, artists and creatives. If you are involved in any initiative that benefits the collective, we would love to support you. This is a conscious renaissance.</p>
</section>

<!-- Slide 4: What we envision -->
<section class="slide s-vision" style="top:2016px">
  <div class="bg-space" role="img" aria-label="Dark starry night backdrop"></div>
  <div class="brand"><div class="brand-name">LUMEN</div><div class="brand-sub">Lantern Circle</div></div>
  <h2 class="abs slide-title vision-title">What we envision</h2>
  <div class="vision-card card-people">
    <div class="photo photo-people" role="img" aria-label="Two children seen from behind in a field of lavender"></div>
    <h3>PEOPLE</h3>
    <p>A World that meets the needs of every human being as a birth right, providing the foundation for self-actualization.</p>
  </div>
  <div class="vision-card card-planet">
    <div class="photo photo-planet" role="img" aria-label="Planet Earth glowing in a purple cosmic frame"></div>
    <h3>PLANET</h3>
    <p>A World that lives in harmony with nature, respects and protects Mother Earth and the Animal Kingdom.</p>
  </div>
  <div class="vision-card card-peace">
    <div class="photo photo-peace" role="img" aria-label="A bird with spread wings flying into a golden sunset"></div>
    <h3>PEACE</h3>
    <p>A World that chooses peace, love and harmony, awake and aware of its connection with everything.</p>
  </div>
</section>

<!-- Slide 5: Partners -->
<section class="slide s-partners" style="top:2680px">
  <div class="bg-space" role="img" aria-label="Night sky with a glowing galaxy rising over the horizon"></div>
  <div class="brand"><div class="brand-name">LUMEN</div><div class="brand-sub">Lantern Circle</div></div>
  <h2 class="abs slide-title partners-title">Partners</h2>
  <div class="partner" style="left:104px;top:146px"><div class="hex hex-violet"></div><span>LANTERN CIRCLE</span></div>
  <div class="partner" style="left:284px;top:146px"><div class="hex hex-green"></div><span>SPROUTLY</span></div>
  <div class="partner" style="left:477px;top:146px"><div class="hex hex-gold"></div><span>KINDRED FIRST</span></div>
  <div class="partner" style="left:670px;top:146px"><div class="hex hex-blue"></div><span>MAKERS WEAVE</span></div>
  <div class="partner" style="left:850px;top:146px"><div class="hex hex-white"></div><span>MYCELIA</span></div>
  <div class="partner" style="left:284px;top:364px"><div class="hex hex-night"></div><span>VANTA</span></div>
  <div class="partner" style="left:477px;top:364px"><div class="hex hex-white"></div><span>RENEWAL</span></div>
  <div class="partner" style="left:670px;top:364px"><div class="hex hex-white"></div><span>LILAC</span></div>
</section>

<!-- Slide 6: Universal laws / Thank you -->
<section class="slide s-laws" style="top:3344px">
  <div class="abs laws-visual" role="img" aria-label="Ringed planet hanging over a violet and orange cloudscape"></div>
  <div class="brand"><div class="brand-name">LUMEN</div><div class="brand-sub">Lantern Circle</div></div>
  <h2 class="abs slide-title laws-title">Universal laws</h2>
  <p class="abs laws-copy">The Universe is perfectly balanced by natural and moral laws, which are regulatory vibrations to maintain order. When we operate within the laws, we can be assured of eventual positive outcomes. When we operate outside of the laws, suffering occurs. The purpose of the laws is to teach a harmonious way to live, which will be in alignment with the greatest good of all, individually and collectively.</p>
  <h2 class="abs slide-title thanks-title">Thank you</h2>
  <div class="contact contact-addr">
    <span class="ico"><svg width="18" height="18" viewBox="0 0 24 24"><path d="M12 2a7 7 0 0 0-7 7c0 5 7 13 7 13s7-8 7-13a7 7 0 0 0-7-7zm0 9.5A2.5 2.5 0 1 1 12 6.5a2.5 2.5 0 0 1 0 5z" fill="#1a0f2b"/></svg></span>
    <span>1422 Lorem ipsum dolor sit amet, consectetur adipiscing elit</span>
  </div>
  <div class="contact contact-phone">
    <span class="ico"><svg width="18" height="18" viewBox="0 0 24 24"><path d="M6.6 10.8a15 15 0 0 0 6.6 6.6l2.2-2.2a1 1 0 0 1 1-.25 11.4 11.4 0 0 0 3.6.57 1 1 0 0 1 1 1V20a1 1 0 0 1-1 1A17 17 0 0 1 3 4a1 1 0 0 1 1-1h3.5a1 1 0 0 1 1 1c0 1.25.2 2.45.57 3.57a1 1 0 0 1-.25 1z" fill="#1a0f2b"/></svg></span>
    <span>+1 000 0000 0000</span>
  </div>
  <div class="contact contact-mail">
    <span class="ico"><svg width="18" height="18" viewBox="0 0 24 24"><rect x="3" y="5" width="18" height="14" rx="2" fill="#1a0f2b"/><path d="M4 7l8 6 8-6" stroke="#fff" stroke-width="1.6" fill="none"/></svg></span>
    <span>info@lanternguildhq.org</span>
  </div>
</section>

</body>
</html>
```